Dovin Sound 862 the new wave for sound to enlighten open ears

This is a music recording studio, we need pictures of a booth, random pictures of anything that will draw interest to a recording studio, we just need the website to reflect a music studio recording website. Apply generic information on the site that correlates with most music studio websites up to date. We want the modern style look that will entice eyes across the nation. Information should be easily accessible on the website. Dovin Sound 862 is owned by Marcellus Okafor located 5176 Bellweather Ln, Miramar, Fl, 33027. Email: Mokaforsound@harnelpost.net and best contact number to date is 417-293-7041. The sound coming out of this location will be radio ready at all times, artist come in one way and come out with more wisdom than before. Its the new way to make music the appropriate way and bring the best out of those willing to reach their peak.

Target Market(s)

Recording Artist

Industry/Entity Type

Recording Studio

Coding

Coded - Design and coding required

Number of Pages Required

1 page

Font styles to use
Sans Serif

Requirements
Must have
• Anything that gives the site a music feel
Nice to have
• microphones, booths, studio mixing desk

```html
<!DOCTYPE html>
<html lang="en">
<head>
<meta charset="utf-8">
<title>Dovin Sound 862 — Music Recording Studio</title>
<link rel="stylesheet" href="https://fonts.googleapis.com/css2?family=Montserrat:wght@400;500;600;700&family=Open+Sans:wght@400;600;700&display=swap">
<style>
:root{
  --teal:#3fbaa2;
  --teal-dark:#2e9f89;
  --navy:#0a2e3f;
  --navy-band:#0d3a4e;
  --navy-bar:#0f4660;
  --ink:#1d2b33;
  --body:#555f66;
  --grey-panel:#efefef;
  --grey-tab:#ececec;
  --line:#dcdcdc;
  --white:#ffffff;
}
*{box-sizing:border-box;margin:0;padding:0}
html,body{width:1200px;height:3152px;overflow:hidden}
body{position:relative;background:var(--white);font-family:"Open Sans",Arial,sans-serif;color:var(--body)}
.abs{position:absolute}
.heading{font-family:"Montserrat",Arial,sans-serif;font-weight:600;text-transform:uppercase;text-align:center}

/* hero */
.hero{left:0;top:0;width:1200px;height:578px;
  background:radial-gradient(ellipse at 50% 45%,#5a3a22 0%,#3a2414 45%,#1a100a 100%);
  clip-path:polygon(0 0,1200px 0,1200px 515px,600px 578px,0 515px)}
.topbar{left:0;top:0;width:1200px;height:109px;background:rgba(43,140,120,.72)}
.brand{left:99px;top:26px;display:flex;align-items:center;gap:14px;color:var(--white);
  font-family:"Montserrat",Arial,sans-serif;font-weight:700;font-size:27px;line-height:30px;text-transform:uppercase}
.brand .dot{width:40px;height:40px;border-radius:50%;background:var(--white)}
.socials{display:flex;gap:10px}
.socials span{width:32px;height:32px;border-radius:50%;border:2px solid var(--white)}
.topbar .socials{position:absolute;left:909px;top:16px}
.nav{right:99px;top:70px;display:flex;gap:22px;font-family:"Montserrat",Arial,sans-serif;font-weight:600;font-size:15px;color:var(--white);text-transform:uppercase}
.hero-title{left:0;width:1200px;top:218px;color:var(--white);font-size:42px;font-weight:700}
.hero-sub{left:0;width:1200px;top:282px;color:var(--white);font-family:"Montserrat",Arial,sans-serif;font-size:32px;font-weight:500;text-align:center}
.btn-outline-light{left:523px;top:363px;width:151px;height:49px;border:2px solid var(--white);color:var(--white);
  font-family:"Montserrat",Arial,sans-serif;font-weight:600;font-size:17px;display:flex;align-items:center;justify-content:center;text-transform:uppercase}
.slider-dots{left:556px;top:453px;display:flex;gap:6px}
.slider-dots span{width:14px;height:14px;border-radius:50%;border:2px solid var(--white)}
.slider-dots span.on{background:var(--teal);border-color:var(--teal)}

/* services */
.section-title{left:0;width:1200px;color:var(--teal);font-size:28px}
.intro{left:195px;width:810px;top:727px;font-size:14px;line-height:26px;text-align:center}
.service{width:260px;text-align:center}
.service .ring{width:164px;height:164px;margin:0 auto;border-radius:50%;border:3px solid var(--navy);display:flex;align-items:center;justify-content:center}
.service .ring.active{border-color:var(--teal)}
.service .ring.active .disc{width:146px;height:146px;border-radius:50%;background:var(--teal);display:flex;align-items:center;justify-content:center}
.service h3{margin-top:20px;font-family:"Montserrat",Arial,sans-serif;font-weight:600;font-size:16px;color:var(--ink);text-transform:uppercase}
.service h3.active{color:var(--teal)}
.service p{margin-top:16px;padding:0 21px;font-size:13.5px;line-height:24px}
.pill{display:inline-flex;margin-top:18px;width:112px;height:40px;border-radius:20px;border:2px solid var(--navy);align-items:center;justify-content:center;font-size:13px;font-weight:600;color:var(--ink)}
.pill.solid{background:var(--teal);border-color:var(--teal);color:var(--white)}

/* booth */
.booth{left:0;top:1201px;width:1200px;height:521px;background:linear-gradient(180deg,#0e3b50 0%,#0b3346 100%)}
.booth-title{left:0;width:1200px;top:1267px;color:var(--white);font-size:28px}
.rule{height:3px;width:136px;left:532px}
.booth-card{top:1399px;width:320px;height:247px;border:3px solid var(--white);overflow:hidden}
.booth-card .photo{position:absolute;inset:0}
.booth-card .tab{position:absolute;left:0;bottom:0;width:314px;height:76px;background:var(--white);clip-path:polygon(0 100%,50% 0,100% 100%)}
.booth-card .label{position:absolute;left:0;width:100%;bottom:12px;text-align:center;font-family:"Montserrat",Arial,sans-serif;font-weight:600;font-size:17px;color:var(--ink)}

/* pricing */
.tabs{left:99px;top:1903px;width:1001px;height:71px;display:flex}
.tabs div{flex:1;background:var(--grey-tab);display:flex;align-items:center;justify-content:center;font-family:"Montserrat",Arial,sans-serif;font-weight:600;font-size:23px;color:var(--ink);text-transform:uppercase}
.tabs div.on{background:var(--teal);color:var(--white);position:relative}
.tabs div.on::after{content:"";position:absolute;left:50%;bottom:-22px;margin-left:-22px;border:22px solid transparent;border-bottom:0;border-top-color:var(--teal)}
.price-col{background:var(--grey-panel);padding:16px 20px 0;text-align:center}
.price-col .row{border-bottom:1px solid var(--line);font-size:13.5px;line-height:27px;padding:10px 0 12px}
.price-col .row:last-of-type{border-bottom:0}
.price-col .pill{margin-top:10px;width:116px;height:38px;font-size:13px}
.price-col.featured{background:var(--teal);color:var(--white);box-shadow:0 6px 16px rgba(0,0,0,.22);padding:24px 30px 0}
.price-col.featured .row{border-bottom-color:rgba(255,255,255,.35);font-size:13px}
.badge{display:inline-block;background:var(--white);color:var(--teal);font-family:"Montserrat",Arial,sans-serif;font-weight:700;font-size:19px;padding:8px 18px;margin-bottom:14px}
.price-col.featured .pill{border-color:var(--white);color:var(--white);margin-top:34px}
.divider{left:99px;top:2577px;width:1001px;height:2px;background:var(--line)}
.partners{left:99px;top:2625px;display:flex;gap:39px}
.partners span{width:133px;height:88px;border:1px solid var(--line);display:flex;align-items:center;justify-content:center}
.partners i{display:block;width:70px;height:26px;background:#c9cfd3;border-radius:3px}

/* footer */
.footer{left:0;top:2753px;width:1200px;height:334px;background:var(--navy);color:var(--white)}
.footer h4{font-family:"Montserrat",Arial,sans-serif;font-weight:600;font-size:16px;text-transform:uppercase;position:absolute;top:50px}
.links{position:absolute;left:393px;top:102px;list-style:none;font-size:14px;line-height:31.5px}
.links li::before{content:"› "}
.contact-item{position:absolute;left:578px;display:flex;gap:16px;font-size:12.5px;line-height:20px}
.contact-item .ico{width:40px;height:40px;border-radius:50%;border:2px solid var(--white);flex:none;display:flex;align-items:center;justify-content:center}
.contact-item b{display:block;font-size:14px}
.field{position:absolute;border:1.5px solid var(--white);font-size:11px;padding:8px 10px;color:var(--white)}
.send{position:absolute;left:846px;top:217px;width:120px;height:38px;border:2px solid var(--white);background:var(--navy-bar);font-size:11.5px;display:flex;align-items:center;justify-content:center;text-transform:uppercase}
.bottom-bar{left:0;top:3087px;width:1200px;height:65px;background:var(--navy-bar);color:var(--white)}
.bottom-bar p{position:absolute;left:99px;top:22px;font-size:13px;font-weight:600}
.bottom-bar .socials{position:absolute;left:950px;top:16px}
</style>
</head>
<body>

<header>
  <div class="abs hero" role="img" aria-label="Photo of a recording studio control room with a large mixing desk and monitors"></div>
  <div class="abs topbar">
    <div class="abs brand"><span class="dot"></span><span>Dovin<br>Sound 862</span></div>
    <div class="socials"><span></span><span></span><span></span><span></span><span></span></div>
    <nav class="abs nav"><span>Home</span><span>Recordings</span><span>About Us</span><span>Pricing</span><span>Portfolio</span><span>Blog</span><span>Contact</span></nav>
  </div>
  <h1 class="abs heading hero-title">Dovin Sound 862</h1>
  <p class="abs hero-sub">We are a music recording studio</p>
  <a class="abs btn-outline-light">Record Now</a>
  <div class="abs slider-dots"><span class="on"></span><span></span><span></span><span></span><span></span></div>
</header>

<section>
  <h2 class="abs heading section-title" style="top:673px">Our Musical Services</h2>
  <p class="abs intro">Nemo enim ipsam voluptatem quia voluptas sit aspernatur aut odit aut fugit, sed quia consequuntur magni dolores eos qui ratione voluptatem sequi nesciunt.</p>

  <div class="abs service" style="left:181px;top:812px">
    <div class="ring">
      <svg width="74" height="74" viewBox="0 0 74 74"><rect x="14" y="4" width="56" height="56" fill="none" stroke="#0a2e3f" stroke-width="4"/><rect x="4" y="14" width="56" height="56" fill="#0a2e3f"/><path d="M26 56V30l18-4v24" stroke="#fff" stroke-width="3" fill="none"/><circle cx="23" cy="56" r="5" fill="#fff"/><circle cx="41" cy="51" r="5" fill="#fff"/></svg>
    </div>
    <h3>Recording Studio</h3>
    <p>Nemo enim ipsam voluptatem quia voluptas sit aspernatur aut odit aut fugit voluptatem.</p>
    <span class="pill">Learn More</span>
  </div>

  <div class="abs service" style="left:490px;top:812px">
    <div class="ring active"><div class="disc">
      <svg width="80" height="80" viewBox="0 0 80 80"><g stroke="#fff" stroke-width="5"><path d="M6 14h44M6 28h44M6 42h24"/></g><path d="M40 66V36l14 6" stroke="#fff" stroke-width="5" fill="none"/><circle cx="33" cy="66" r="9" fill="#fff"/><path d="M56 48l18 13-18 13z" fill="#fff"/></svg>
    </div></div>
    <h3 class="active">Music Studio</h3>
    <p>Nemo enim ipsam voluptatem quia voluptas sit aspernatur aut odit aut fugit voluptatem.</p>
    <span class="pill solid">Learn More</span>
  </div>

  <div class="abs service" style="left:757px;top:812px">
    <div class="ring">
      <svg width="80" height="70" viewBox="0 0 80 70"><circle cx="44" cy="35" r="32" fill="#0a2e3f"/><circle cx="50" cy="35" r="8" fill="#fff"/><rect x="2" y="3" width="46" height="64" fill="#0a2e3f" stroke="#fff" stroke-width="3"/><path d="M24 50V20l12 4" stroke="#fff" stroke-width="4" fill="none"/><circle cx="19" cy="50" r="6" fill="#fff"/></svg>
    </div>
    <h3>Music Recording</h3>
    <p>Nemo enim ipsam voluptatem quia voluptas sit aspernatur aut odit aut fugit voluptatem.</p>
    <span class="pill">Learn More</span>
  </div>
</section>

<section>
  <div class="abs booth"></div>
  <h2 class="abs heading booth-title">Our Recording Booth</h2>
  <div class="abs rule" style="top:1321px;background:var(--white)"></div>

  <div class="abs booth-card" style="left:99px">
    <div class="photo" role="img" aria-label="Producer seated at a studio desk with keyboard and monitors" style="background:linear-gradient(160deg,#4a4640,#2a2522 60%,#5b2f2c)"></div>
    <div class="tab"></div><div class="label">Recording Studio</div>
  </div>
  <div class="abs booth-card" style="left:439px">
    <div class="photo" role="img" aria-label="Singer with guitar recording at a microphone in a vocal booth" style="background:linear-gradient(160deg,#3e3a35,#6b5a48 55%,#2b2723)"></div>
    <div class="tab"></div><div class="label">Music Recording</div>
  </div>
  <div class="abs booth-card" style="left:779px">
    <div class="photo" role="img" aria-label="Headphones resting on a mixing console" style="background:linear-gradient(160deg,#3a5c9a,#6a7fb8 50%,#c79a5a)"></div>
    <div class="tab"></div><div class="label">Music Studio</div>
  </div>
</section>

<section>
  <h2 class="abs heading section-title" style="top:1790px">Our Musical Services</h2>
  <div class="abs rule" style="top:1838px;width:120px;left:540px;height:2px;background:var(--teal)"></div>

  <div class="abs tabs"><div>Recording Price</div><div class="on">Memberships Deals</div><div>Mix Down Only Prices</div></div>

  <div class="abs price-col" style="left:147px;top:2012px;width:290px;height:456px">
    <div class="row">$80 per hour minimum 4 hours required</div>
    <div class="row">75$ per hour minimum 8 hours required</div>
    <div class="row">$70 per hour minimum 12 hours required</div>
    <div class="row">$90 for individual hours , packages recommended</div>
    <span class="pill">Get Now</span>
  </div>

  <div class="abs price-col featured" style="left:437px;top:2033px;width:324px;height:472px">
    <span class="badge">POPULAR</span>
    <div class="row">$1500, get 48 recording hours in addition to 24 hours mix down</div>
    <div class="row">$2500, get 72 recording hours in addition to 48 hours mix down</div>
    <div class="row">$3500, get 96 recording hours in addition to 72 hours mix down</div>
    <span class="pill">Get Now</span>
  </div>

  <div class="abs price-col" style="left:761px;top:2012px;width:290px;height:456px">
    <div class="row">$50 per hour minimum 4 hours required</div>
    <div class="row">$45 per hour minimum 8 hours required</div>
    <div class="row">$40 per hour minimum 12 hours required</div>
    <div class="row">$60 for individual hours, packages recommended</div>
    <span class="pill">Get Now</span>
  </div>

  <div class="abs divider"></div>
  <div class="abs partners"><span><i></i></span><span><i></i></span><span><i></i></span><span><i></i></span><span><i></i></span><span><i></i></span></div>
</section>

<footer>
  <div class="abs footer">
    <div class="abs brand" style="top:146px"><span class="dot"></span><span>Dovin<br>Sound 862</span></div>

    <h4 style="left:393px">Quick Links</h4>
    <ul class="links"><li>Home</li><li>Recordings</li><li>Pricing</li><li>About Us</li><li>Portfolio</li><li>Contact Us</li></ul>

    <h4 style="left:578px">Contact Us</h4>
    <div class="contact-item" style="top:104px">
      <span class="ico"><svg width="14" height="18" viewBox="0 0 14 18"><path d="M7 17C3 11 1 9 1 6.5a6 6 0 0 1 12 0C13 9 11 11 7 17z" fill="none" stroke="#fff" stroke-width="2"/><circle cx="7" cy="6.5" r="2" fill="#fff"/></svg></span>
      <div><b>COMPANY,</b>5176 Bellweather Ln, Miramar,<br>Fl, 33027.</div>
    </div>
    <div class="contact-item" style="top:180px">
      <span class="ico"><svg width="12" height="18" viewBox="0 0 12 18"><rect x="1" y="1" width="10" height="16" rx="2" fill="none" stroke="#fff" stroke-width="2"/><circle cx="6" cy="14" r="1" fill="#fff"/></svg></span>
      <div><b>PHONE:</b>417-293-7041</div>
    </div>
    <div class="contact-item" style="top:240px">
      <span class="ico"><svg width="18" height="13" viewBox="0 0 18 13"><rect x="1" y="1" width="16" height="11" fill="none" stroke="#fff" stroke-width="2"/><path d="M1 1l8 6 8-6" fill="none" stroke="#fff" stroke-width="2"/></svg></span>
      <div><b>Mail:</b>Mokaforsound@harnelpost.net</div>
    </div>

    <h4 style="left:846px">Contact Form</h4>
    <div class="field" style="left:846px;top:94px;width:122px;height:36px">Name</div>
    <div class="field" style="left:978px;top:94px;width:122px;height:36px">Phone</div>
    <div class="field" style="left:846px;top:140px;width:254px;height:66px">Message</div>
    <div class="send">Send Message</div>
  </div>
  <div class="abs bottom-bar">
    <p>Copyright © 2017 Dovin Sound 862. All Right Reserved</p>
    <div class="socials"><span></span><span></span><span></span><span></span></div>
  </div>
</footer>

</body>
</html>
```